co working space / serviced office/ business centre

Brevlo - brevlo.in, is a very young brand bieng run by 3 young entrepreneurs. We want to be become out of the league company delivering fabulous and beautiful serviced offices in India and abroad. We hire designers who have made spaces across the world. We want to get visiting card design which gives complete fresh look to the people who carries that card, has to be very impactful and should symbolise happy young and energetic brand. should be completely out of the box thinking of international level, should portray global brand image.

Target Market(s)

Startups, (Small, medium and large corporates)

Industry/Entity Type

Business

Contact Information for Business Card

Name, Email, Address, Mobile number, Landline number, website

Colors

Designer to choose colors to be used in the design.

Requirements
Must have
• Nice new shape
Nice to have
• We want creative cuts, different size and impactful brand clarity
Should not have
• Boring and regular design and shape

```html
<!DOCTYPE html>
<html lang="en">
<head>
<meta charset="utf-8">
<title>Brevlo Business Card</title>
<link href="https://fonts.googleapis.com/css2?family=Work+Sans:wght@400;500;600;700&display=swap" rel="stylesheet">
<style>
  :root {
    --brand-red: #ec1c24;
    --ink: #3a3a3a;
    --ink-soft: #555555;
    --charcoal: #3d3d3f;
    --paper: #ffffff;
    --backdrop: #e9e9e7;
  }
  * { margin: 0; padding: 0; box-sizing: border-box; }
  html, body {
    width: 1200px; height: 1000px; overflow: hidden;
    background: var(--backdrop);
    font-family: "Work Sans", sans-serif;
  }
  .canvas { position: relative; width: 1200px; height: 1000px; }

  .card {
    position: absolute; left: 255px; width: 665px; height: 380px;
    border-radius: 18px; overflow: hidden;
    box-shadow: 0 4px 12px rgba(0,0,0,0.18);
  }
  .card--front { top: 100px; background: var(--paper); }
  .card--back { top: 519px; background: var(--brand-red); }

  .lockup { position: absolute; text-align: center; }
  .card--front .lockup { left: 47px; top: 108px; width: 256px; color: var(--brand-red); }
  .card--back .lockup { left: 210px; top: 108px; width: 256px; color: var(--paper); }
  .lockup__dot {
    width: 56px; height: 56px; border-radius: 50%;
    background: currentColor; margin: 0 auto 14px;
  }
  .lockup__name {
    font-weight: 700; font-size: 46px; line-height: 1; letter-spacing: 2px;
  }
  .lockup__rule { height: 3px; background: currentColor; margin: 14px 0 10px; }
  .lockup__tagline {
    font-weight: 600; font-size: 13px; letter-spacing: 2.6px;
  }

  .divider {
    position: absolute; left: 342px; top: 100px; width: 2px; height: 180px;
    background: var(--brand-red);
  }
  .contact { position: absolute; left: 380px; top: 96px; color: var(--ink-soft); }
  .contact__name {
    color: var(--brand-red); font-size: 24px; font-weight: 400; letter-spacing: 1.5px; line-height: 1.1;
  }
  .contact__role { color: var(--ink); font-size: 15px; font-weight: 500; margin-top: 6px; }
  .contact__address { font-size: 15px; line-height: 21px; margin-top: 16px; }
  .contact__list { list-style: none; font-size: 15px; line-height: 19.5px; margin-top: 18px; }
  .contact__list li { display: flex; align-items: center; gap: 8px; }
  .contact__list svg { width: 10px; height: 10px; fill: var(--brand-red); flex: none; }

  .corner-bands { position: absolute; left: 0; bottom: 0; width: 665px; height: 34px; }

  .card__website {
    position: absolute; left: 0; right: 0; top: 334px; text-align: center;
    color: var(--paper); font-size: 15px; letter-spacing: 1.2px;
  }
</style>
</head>
<body>
<main class="canvas">

  <section class="card card--front" aria-label="Business card front">
    <div class="lockup">
      <div class="lockup__dot"></div>
      <div class="lockup__name">BREVLO</div>
      <div class="lockup__rule"></div>
      <div class="lockup__tagline">MEET. PLAN. GROW</div>
    </div>

    <div class="divider"></div>

    <div class="contact">
      <h1 class="contact__name">DANIEL OKAFOR</h1>
      <p class="contact__role">Founder</p>
      <p class="contact__address">48 Harbour Line Rd.<br>Bayview, CA 90412</p>
      <ul class="contact__list">
        <li><svg viewBox="0 0 10 10"><path d="M2 0.5 L3.6 0.5 L4.2 2.8 L3 3.8 C3.6 5.2 4.8 6.4 6.2 7 L7.2 5.8 L9.5 6.4 L9.5 8 C9.5 9 8.8 9.5 8 9.5 C4 9.2 0.8 6 0.5 2 C0.5 1.2 1 0.5 2 0.5 Z"/></svg>415-208-3361</li>
        <li><svg viewBox="0 0 10 10"><path d="M0.5 2 H9.5 V8.5 H0.5 Z M1.5 3 V7.5 H8.5 V3 L5 5.6 Z M2 3 L5 5 L8 3 Z" fill-rule="evenodd"/></svg>hello@brevlo.in</li>
        <li><svg viewBox="0 0 10 10"><circle cx="5" cy="5" r="4.5"/><path d="M0.5 5 H9.5 M5 0.5 V9.5" stroke="#fff" stroke-width="0.8"/></svg>www.brevlo.in</li>
      </ul>
    </div>

    <svg class="corner-bands" viewBox="0 0 665 34" aria-hidden="true">
      <rect x="0" y="18" width="345" height="16" fill="var(--charcoal)"/>
      <polygon points="335,34 350,18 353,18 338,34" fill="var(--paper)"/>
      <polygon points="338,34 372,0 665,0 665,34" fill="var(--brand-red)"/>
    </svg>
  </section>

  <section class="card card--back" aria-label="Business card back">
    <div class="lockup">
      <div class="lockup__dot"></div>
      <div class="lockup__name">BREVLO</div>
      <div class="lockup__rule"></div>
      <div class="lockup__tagline">MEET. PLAN. GROW</div>
    </div>
    <p class="card__website">www.yourwebsite.com</p>
  </section>

</main>
</body>
</html>
```